Vennekamp.dk - FellowCup

I need a design for a WordPress site that serves to inform and present the national golfchampionship for colleagues in Denmark. The sites need to be visual stuninng or big, and it doesnt have a lot of pages. Maybe 5-6 regular text pages and not a lot of navigation. It should be a simple and powerfull site.

The sites need to present and sell the tournament, and have a clear call to action button "Sign up" (Tilmeld) and resultscoring.

If you can make a logo and visual ID for the tournament as well that would be a bonus.

Target Market(s)

Golfers

Logo Text

Vennekamp

Number of Pages Required

3 page

Requirements
Must have
• A frontpage
• Button 1 - Tilmeld (danish for sign up)
• Button 2 - Resultater (results)
Nice to have
• Logo
• A style we can use offline as well

```html
<!DOCTYPE html>
<html lang="da">
<head>
<meta charset="utf-8">
<title>Vennekamp – FellowCup</title>
<link href="https://fonts.googleapis.com/css2?family=Exo+2:wght@300;400;500;600&family=Cabin:wght@400;500&display=swap" rel="stylesheet">
<style>
:root{
  --red:#ff0a0a;
  --yellow:#ffe100;
  --gold:#d9a90a;
  --blue:#0a74bb;
  --link-blue:#1a78b8;
  --green:#6cbf1e;
  --ink:#333;
  --grey-text:#444;
  --footer-bg:#ececec;
  --rule:#d6d6d6;
}
*{box-sizing:border-box;margin:0;padding:0}
html,body{width:1200px;height:2214px;overflow:hidden;background:#fff}
body{position:relative;font-family:"Cabin",sans-serif;color:var(--ink)}
.abs{position:absolute}

/* header */
.site-header{left:0;top:0;width:1200px;height:130px;background:#fff}
.brand{left:74px;top:30px;display:flex;align-items:center;gap:16px}
.brand-dot{width:68px;height:68px;border-radius:50%;background:var(--blue)}
.brand-name{font-family:"Exo 2",sans-serif;font-weight:600;font-size:20px;line-height:21px;letter-spacing:1px;color:#222;text-transform:uppercase}
.main-nav{left:379px;top:40px;display:flex;gap:18px;font-family:"Exo 2",sans-serif;font-size:18px;color:#333}
.btn{display:flex;align-items:center;justify-content:center;gap:18px;font-family:"Exo 2",sans-serif;font-size:20px;border-radius:6px;text-transform:uppercase}
.btn-red{background:var(--red);color:#fff}
.btn-yellow{background:var(--yellow);color:#111}
.nav-btn{top:23px;width:147px;height:53px;font-size:19px}

/* hero */
.hero{left:0;top:110px;width:1200px;height:662px;background:linear-gradient(180deg,#7f8a6f 0%,#6f8a4c 35%,#6f9242 60%,#7ea74c 100%)}
.hero-shade{left:0;top:110px;width:1200px;height:662px;background:rgba(0,0,0,.18)}
.hero-wave{left:0;top:100px}
.hero-title{left:0;top:306px;width:1200px;text-align:center;font-family:"Exo 2",sans-serif;font-weight:400;font-size:35px;line-height:37px;color:#fff}
.hero-dates{left:0;top:498px;width:1200px;text-align:center;font-family:"Cabin",sans-serif;font-size:21px;line-height:25px;color:#fff}
.cta-btn{width:225px;height:59px;font-size:23px}

/* photo strip */
.photo{top:774px;height:246px}
.photo-1{left:0;width:398px;background:linear-gradient(180deg,#5e7d6e,#5d8b3f)}
.photo-2{left:401px;width:398px;background:linear-gradient(180deg,#b7bcc0,#6f9646)}
.photo-3{left:802px;width:398px;background:linear-gradient(180deg,#4f6a3a,#79a548)}

/* blue band */
.promo-band{left:0;top:1020px;width:1200px;height:105px;background:var(--blue);color:#fff}
.promo-title{left:107px;top:30px;font-family:"Exo 2",sans-serif;font-weight:400;font-size:31px}
.promo-text{left:413px;top:32px;width:480px;font-size:15.5px;line-height:24px}
.promo-link{left:920px;top:32px;font-size:15.5px;line-height:24px}

/* info grid */
.info-item{width:335px}
.info-item h3{font-family:"Exo 2",sans-serif;font-weight:400;font-size:23px;line-height:32px;color:var(--link-blue);min-height:64px;max-width:310px}
.info-row-2 h3{min-height:96px}
.info-item h3.plain{color:#333}
.info-item hr{border:0;border-top:1px solid var(--rule);margin-top:10px}
.info-item p{margin-top:16px;font-size:14px;line-height:24px;color:var(--grey-text);padding-left:2px}

/* footer */
.footer-wave{left:0;top:1855px}
.site-footer{left:0;top:1900px;width:1200px;height:314px;background:var(--footer-bg)}
.partner-a{left:75px;top:1963px;width:76px;height:76px;border-radius:50%;background:#e31b23}
.partner-b{left:183px;top:1972px;width:115px;height:66px;background:#d9e7ef}
.contact-label{font-size:12px;color:#666;text-transform:uppercase;letter-spacing:.5px}
.contact-value{font-size:19px;line-height:23px;color:#444;margin-top:4px}
.message-btn{left:812px;top:2037px;width:122px;height:31px;border-radius:16px;background:#e52421;color:#fff;font-family:"Exo 2",sans-serif;font-weight:600;font-size:14px;display:flex;align-items:center;justify-content:center}
.social{top:2088px;width:33px;height:33px;border-radius:50%;border:2px solid #555}
.copyright{left:0;top:2170px;width:1200px;text-align:center;font-size:14px;color:#555}
</style>
</head>
<body>

<header class="site-header abs">
  <div class="brand abs"><span class="brand-dot"></span><span class="brand-name">Holdsport<br>Forbund</span></div>
  <nav class="main-nav abs"><span>HOME</span><span>ABOUT US</span><span>TOURNAMENT</span><span>CONTACT US</span></nav>
  <a class="btn btn-red nav-btn abs" style="left:821px">Tilmeld</a>
  <a class="btn btn-yellow nav-btn abs" style="left:977px">Resultater</a>
</header>

<section class="hero abs" role="img" aria-label="Golfspiller set bagfra der holder flagstangen, mens en holdkammerat putter på greenen"></section>
<div class="hero-shade abs"></div>
<svg class="hero-wave abs" width="1200" height="60" viewBox="0 0 1200 60">
  <path d="M0 0H1200V20C1000 60 800 -5 600 25C400 55 200 10 0 32Z" fill="#fff"/>
  <path d="M0 32C200 10 400 55 600 25C800 -5 1000 60 1200 20" fill="none" stroke="var(--gold)" stroke-width="9"/>
</svg>
<h1 class="hero-title abs">Lav et hold og kom rundt på de<br>danske golfbaner i firmaidrættens<br>sjove holdturnering!</h1>
<p class="hero-dates abs">Turneringsstart<br>den 22. april – finalestævne, den 21. september</p>
<a class="btn btn-red cta-btn abs" style="left:370px;top:633px">Tilmeld
  <svg width="34" height="20" viewBox="0 0 34 20"><path d="M1 10H31M22 1L31 10L22 19" fill="none" stroke="currentColor" stroke-width="2.5"/></svg></a>
<a class="btn btn-yellow cta-btn abs" style="left:605px;top:633px">Resultater
  <svg width="34" height="20" viewBox="0 0 34 20"><path d="M1 10H31M22 1L31 10L22 19" fill="none" stroke="currentColor" stroke-width="2.5"/></svg></a>

<div class="photo photo-1 abs" role="img" aria-label="To golfspillere ved en sø studerer en bold i græsset"></div>
<div class="photo photo-2 abs" role="img" aria-label="Golfspiller slår ud, mens medspillere med trolleys venter"></div>
<div class="photo photo-3 abs" role="img" aria-label="Spiller putter på greenen ved flaget"></div>

<section class="promo-band abs">
  <h2 class="promo-title abs">Freelance-golfer?</h2>
  <p class="promo-text abs">Så kan du deltage i Danmarks eneste landsdækkende Pay and Play turnering for hold.</p>
  <p class="promo-link abs">Se mere på<br>www.spilfrit2012.dk</p>
</section>

<article class="info-item abs" style="left:71px;top:1165px">
  <h3>Hold på 2-4 spillere</h3><hr>
  <p>Et hold består af 2-4 spillere, hvor I er to spillere fra holdet pr. match. Turneringen kører i puljer af 5-6 hold, som er delt op geografisk, efter hvor i landet I og de andre hold kommer fra. Turneringen er åben for alle klubspillere med amatør-status, og spilleformen er four-ball stableford.</p>
</article>
<article class="info-item abs" style="left:432px;top:1165px">
  <h3>Bestem selv, hvor og hvornår matchen skal spilles</h3><hr>
  <p>I Vennekamp har I chancen for at komme rundt og prøve at spille på flere af landets golfbaner. I bestemmer nemlig selv sted og tid for hver match i fællesskab med det hold, I skal møde. Matchen skal blot være spillet inden for en stopdato for hver af de 5 runder i turneringen.</p>
</article>
<article class="info-item abs" style="left:793px;top:1165px">
  <h3>Tilmeld jer senest den 15. april</h3><hr>
  <p>Tag fat i dine kolleger og tilmeld jer på www.vennekamp.dk – senest den 15. april 2012.</p>
</article>
<article class="info-item info-row-2 abs" style="left:71px;top:1472px">
  <h3>Finalestævne på Lindholt Golfbane</h3><hr>
  <p>Vinderne fra hver pulje kan deltage i finalestævnet, som spilles den 21. september på Lindholt Golfbane. Der er flotte præmier til alle puljevindere og til de tre bedste i finalestævnet.</p>
</article>
<article class="info-item info-row-2 abs" style="left:432px;top:1472px">
  <h3>1. præmie: Weekendophold for hele holdet på Havbakke Golf Resort</h3>
</article>
<article class="info-item info-row-2 abs" style="left:793px;top:1472px">
  <h3 class="plain">Kr. 600,- pr. hold</h3>
</article>

<a class="btn btn-red cta-btn abs" style="left:370px;top:1749px">Tilmeld
  <svg width="34" height="20" viewBox="0 0 34 20"><path d="M1 10H31M22 1L31 10L22 19" fill="none" stroke="currentColor" stroke-width="2.5"/></svg></a>
<a class="btn btn-yellow cta-btn abs" style="left:605px;top:1749px">Resultater
  <svg width="34" height="20" viewBox="0 0 34 20"><path d="M1 10H31M22 1L31 10L22 19" fill="none" stroke="currentColor" stroke-width="2.5"/></svg></a>

<footer class="site-footer abs"></footer>
<svg class="footer-wave abs" width="1200" height="60" viewBox="0 0 1200 60">
  <path d="M0 30C200 5 400 5 600 30C800 55 1000 55 1200 20V60H0Z" fill="var(--footer-bg)"/>
  <path d="M0 30C200 5 400 5 600 30C800 55 1000 55 1200 20" fill="none" stroke="var(--green)" stroke-width="9"/>
</svg>

<div class="partner-a abs"></div>
<div class="partner-b abs"></div>

<svg class="abs" style="left:420px;top:1976px" width="34" height="34" viewBox="0 0 24 24"><path d="M6 2L9 6L7 9C8 12 11 15 14 16L17 14L21 17L19 21C11 21 3 13 3 5Z" fill="none" stroke="#555" stroke-width="1.3"/></svg>
<div class="abs" style="left:476px;top:1972px"><div class="contact-label">Call</div><div class="contact-value">40 12 34 56</div></div>
<div class="abs" style="left:606px;top:1972px"><div class="contact-label">Fax</div><div class="contact-value">40 12 34 57</div></div>
<svg class="abs" style="left:426px;top:2040px" width="28" height="38" viewBox="0 0 20 28"><path d="M10 27C10 27 2 16 2 10A8 8 0 0 1 18 10C18 16 10 27 10 27Z" fill="none" stroke="#555" stroke-width="1.3"/><circle cx="10" cy="10" r="3" fill="none" stroke="#555" stroke-width="1.3"/></svg>
<div class="abs" style="left:476px;top:2036px"><div class="contact-label">Visit</div><div class="contact-value">Bakkevej 7<br>4100 Ringsted</div></div>
<svg class="abs" style="left:756px;top:1974px" width="34" height="34" viewBox="0 0 24 24"><path d="M4 20L5 15L17 3L21 7L9 19Z M15 5L19 9" fill="none" stroke="#555" stroke-width="1.3"/></svg>
<div class="abs" style="left:812px;top:1972px"><div class="contact-label">Write</div><div class="contact-value">kontakt@holdsportforbund.dk</div></div>
<a class="message-btn abs">MESSAGE US</a>
<span class="social abs" style="left:810px" aria-label="Socialt netværk 1"></span>
<span class="social abs" style="left:847px" aria-label="Socialt netværk 2"></span>

<p class="copyright abs">© 2015 holdsportforbund.dk. All rights reserved.</p>

</body>
</html>
```